Health and Fitness Club requires a stunning and simple website

We are a health and fitness club based in Dubai, when we launch we will be the biggest club in the country, we will also have the 2 largest activity rooms in the country, we are setting a new standard in the industry by offering one thing, our attitude.

Our attitude means the following:
unlike other clubs we have no hidden charges or fees
our members can join daily, monthly, 6 months or annually
our service and facility are comparable to 5* hotel gyms
our equipment is second to none
our space is the biggest in the country
we do not force our members to use our in-house personal trainers - you can bring your own and we will not charge them entry!
we will have a cutting edge brawnmesh box in our gym with classes by the best trainers in the country
we will be providing free-lance personal trainers a platform to engage customers, grow their business and even use our activity rooms for classes

Basically we will be a gym like no other, simply because we are gym people and we hate the restrictive practices and hidden charges by other gyms, so we are making our own gym which focuses on quality and service.

All of this has to be communicated in the style of the website, the colors of the website we want to be limited to the logo colors as this will be the same theme running throughout the gym.

The landing page of the website HAS to incorporate elements from our social media presences, this basically is the usual, chirplo, snapvault, kinwall. We can have these as a sidebar, the centre of the page should display the latest article from our blog (also on the website) Also we need to have a calendar for activities and classes on the front page. The menu should have links to the following:
Latest News
About us
Team
Gallery
Membership
Classes
Member Log In
Contact Us
Location

The style of the website has to be similar to the logo, particularly in terms of the fonts used.

```html
<!DOCTYPE html>
<html lang="en">
<head>
<meta charset="utf-8">
<title>Ironhall Health &amp; Fitness Club</title>
<link href="https://fonts.googleapis.com/css2?family=Oswald:wght@400;500;600;700&family=Open+Sans:wght@400;600;700&display=swap" rel="stylesheet">
<style>
:root{
  --red:#c0161f;
  --red-dark:#8f0f16;
  --ink:#2b2b2b;
  --charcoal:#333333;
  --night:#1f1f1f;
  --page:#e6e6e6;
  --white:#ffffff;
  --muted:#7a7a7a;
  --line:#d6d6d6;
  --head:"Oswald",Arial,sans-serif;
  --body:"Open Sans",Arial,sans-serif;
}
*{box-sizing:border-box;margin:0;padding:0}
html,body{width:1200px;height:2164px;overflow:hidden}
body{background:var(--page);font-family:var(--body);color:var(--ink);position:relative;font-size:11px}
.abs{position:absolute}
/* header */
.site-header{left:0;top:0;width:1200px;height:84px;background:linear-gradient(#262626,#3a3a3a)}
.brand{left:150px;top:14px;display:flex;align-items:center;gap:12px}
.brand-dot{width:54px;height:54px;border-radius:50%;background:var(--red)}
.brand-name{font-family:var(--head);font-weight:600;font-size:26px;color:var(--white);letter-spacing:1px}
.social{right:120px;top:24px;display:flex;gap:6px}
.social span{height:26px;padding:0 9px;display:flex;align-items:center;font-size:10px;font-weight:700;color:var(--white);border-radius:3px}
.s-chirp{background:#3aa0d8}.s-snap{background:#7a5a44}.s-kin{background:#3b5a99}.s-stream{background:#c4302b}.s-circ{background:#d44a35}
/* nav */
.main-nav{left:0;top:84px;width:1200px;height:26px;background:var(--white);border-bottom:3px solid var(--red)}
.main-nav ul{list-style:none;display:flex;margin-left:164px;height:100%}
.main-nav li{font-family:var(--head);font-size:11.5px;color:var(--ink);padding:0 14px;display:flex;align-items:center}
.main-nav li.active{background:var(--red);color:var(--white)}
/* hero */
.hero{left:0;top:113px;width:1200px;height:310px;background:linear-gradient(110deg,#5a5a5a 0%,#2e2e2e 45%,#4b4b4b 70%,#1c1c1c 100%)}
.hero-copy{left:180px;top:48px;color:var(--white)}
.hero-copy h1{font-family:var(--head);font-weight:500;font-size:40px;letter-spacing:1px}
.hero-copy p{font-size:12px;margin:6px 0 16px}
.btn{display:inline-block;background:var(--red);color:var(--white);font-size:10px;font-weight:700;padding:7px 14px;text-transform:uppercase}
.hero-arrow{top:130px;width:22px;height:40px;background:var(--red)}
/* features */
.features{left:168px;top:410px;width:864px;height:180px;display:flex;box-shadow:0 2px 6px rgba(0,0,0,.2)}
.upcoming{width:272px;background:var(--white);padding:14px 14px}
.upcoming h3{font-family:var(--head);font-weight:500;color:var(--red);font-size:16px;margin-bottom:8px}
.upcoming .row{display:flex;align-items:center;gap:10px;border-top:1px solid var(--line);padding:8px 0;font-size:10px}
.upcoming .thumb{width:28px;height:22px;background:linear-gradient(#9a9a9a,#555)}
.upcoming .time{margin-left:auto;color:var(--muted)}
.offer{padding:16px 16px;color:var(--white);position:relative}
.offer h3{font-family:var(--head);font-weight:500;font-size:16px;margin-bottom:14px}
.offer .body{display:flex;gap:12px;font-size:10px;line-height:1.5}
.offer .ring{flex:none;width:40px;height:40px;border-radius:50%;border:2px solid rgba(255,255,255,.7);display:flex;align-items:center;justify-content:center}
.offer .btn{position:absolute;right:16px;bottom:16px;background:rgba(0,0,0,.35)}
.membership{width:260px;background:var(--red-dark)}
.training{width:332px;background:var(--red)}
/* about */
.about{left:168px;top:760px;width:864px;height:180px;display:flex}
.about-photo{width:300px;background:linear-gradient(135deg,#c9d6dd,#7d8f99)}
.about-panel{flex:1;background:var(--charcoal);color:var(--white);padding:20px 28px;position:relative}
.about-panel h2{font-family:var(--head);font-weight:500;font-size:40px;letter-spacing:1px;margin-bottom:10px}
.about-panel p{font-size:10px;line-height:1.6;color:#d0d0d0}
.about-panel .btn{position:absolute;right:28px;bottom:18px;padding:9px 18px}
/* articles */
.articles{left:168px;top:968px;width:560px}
.bar{height:30px;background:var(--white);display:flex;align-items:center;padding:0 10px;justify-content:space-between;border-bottom:2px solid var(--ink)}
.bar h2{font-family:var(--head);font-weight:500;font-size:15px}
.bar span{background:#bdbdbd;color:var(--white);font-size:9px;padding:3px 8px}
.article{position:relative;padding-left:88px;margin-top:32px}
.date{position:absolute;left:10px;top:0;width:58px;text-align:center}
.date b{display:block;background:var(--red);color:var(--white);font-family:var(--head);font-size:20px;padding:4px 0}
.date i{display:block;background:var(--ink);color:var(--white);font-style:normal;font-size:9px;padding:3px 0}
.date small{display:block;font-size:8px;color:var(--muted);margin-top:6px;line-height:1.5}
.article .photo{width:472px}
.article h3{font-family:var(--head);font-weight:500;font-size:16px;margin:14px 0 6px}
.article p{font-size:10px;line-height:1.6;color:#555}
.article .btn{float:right;margin-top:10px}
.article::after{content:"";display:block;clear:both}
.ph-1{height:208px;background:linear-gradient(120deg,#3d4b5a,#9aa6b2 50%,#2c3440)}
.ph-2{height:214px;background:linear-gradient(120deg,#e3e1dc,#b99f86 45%,#d8d8d8)}
.ph-3{height:74px;background:linear-gradient(120deg,#a6a6a6,#5f5f5f)}
/* sidebar */
.sidebar{left:744px;top:968px;width:288px}
.widget{background:var(--white);margin-bottom:18px}
.widget-title{background:var(--ink);color:var(--white);font-family:var(--head);font-weight:500;font-size:13px;padding:8px 12px}
.acc{border-bottom:1px solid var(--line);padding:9px 12px;display:flex;justify-content:space-between;align-items:center}
.acc b{font-size:10.5px;font-weight:600}
.acc small{display:block;font-size:8.5px;color:var(--muted)}
.acc .plus{width:16px;height:16px;border:1px solid var(--line);font-size:12px;line-height:14px;text-align:center;color:var(--muted)}
.acc-open{padding:10px 12px;display:flex;gap:10px;border-bottom:1px solid var(--line);font-size:9px;color:#555;line-height:1.5}
.acc-open .thumb{flex:none;width:70px;height:52px;background:linear-gradient(#d8c7b5,#8c7a68)}
.acc-open em{color:var(--red);font-style:normal;font-weight:600}
.calendar{padding:10px 12px 14px}
.calendar .month{text-align:center;font-size:10px;font-weight:600;margin-bottom:6px}
.calendar table{width:100%;border-collapse:collapse;font-size:9px;text-align:center}
.calendar th{background:var(--ink);color:var(--white);padding:5px 0;font-weight:600}
.calendar td{border:1px solid var(--line);padding:5px 0;color:#555}
.calendar td.today{background:var(--red);color:var(--white)}
.insta{display:grid;grid-template-columns:repeat(4,1fr);gap:4px;padding:10px 12px 12px}
.insta div{height:56px}
.g1{background:linear-gradient(#d9b9a2,#8b5f4c)}.g2{background:linear-gradient(#c6ced6,#69737d)}.g3{background:linear-gradient(#e3c3b0,#a4473c)}.g4{background:linear-gradient(#bfc9c2,#66766b)}
/* footer */
.site-footer{left:0;top:1992px;width:1200px;height:172px;background:var(--night);color:#bdbdbd}
.footer-cols{left:168px;top:14px;width:864px;display:flex;gap:40px;font-size:9.5px;line-height:1.8}
.footer-cols h4{font-family:var(--head);font-weight:500;color:var(--white);font-size:13px;margin-bottom:6px}
.footer-cols .contact{width:210px}
.footer-cols .links{width:250px;display:flex;gap:40px}
.footer-cols .news{flex:1}
.news form{display:flex;margin-top:8px}
.news .field{flex:1;height:26px;background:#3a3a3a}
.news .btn{padding:7px 16px}
.copyright{left:0;bottom:0;width:1200px;height:24px;border-top:1px solid #333;text-align:center;font-size:8.5px;line-height:24px;color:#888}
</style>
</head>
<body>

<header class="site-header abs">
  <div class="brand abs"><div class="brand-dot"></div><div class="brand-name">IRONHALL</div></div>
  <div class="social abs">
    <span class="s-chirp">chirplo</span><span class="s-snap">snapvault</span><span class="s-kin">kinwall</span><span class="s-circ">circlet</span><span class="s-stream">streamly</span>
  </div>
</header>

<nav class="main-nav abs">
  <ul>
    <li class="active">HOME</li><li>LATEST NEWS</li><li>ABOUT US</li><li>TEAM</li><li>GALLERY</li><li>MEMBERSHIP</li><li>CLASSES</li><li>MEMBER LOG IN</li><li>CONTACT US</li><li>LOCATION</li>
  </ul>
</nav>

<section class="hero abs" role="img" aria-label="Close-up of dumbbell racks in the gym">
  <div class="hero-copy abs">
    <h1>GROUP CLASSES</h1>
    <p>Unlimited group classes for every member, every day</p>
    <span class="btn">More Details</span>
  </div>
  <div class="hero-arrow abs" style="left:0"><svg width="22" height="40"><path d="M14 13l-6 7 6 7" stroke="#fff" stroke-width="2.5" fill="none"/></svg></div>
  <div class="hero-arrow abs" style="right:0"><svg width="22" height="40"><path d="M8 13l6 7-6 7" stroke="#fff" stroke-width="2.5" fill="none"/></svg></div>
</section>

<section class="features abs">
  <div class="upcoming">
    <h3>Upcoming Classes</h3>
    <div class="row"><div class="thumb" role="img" aria-label="Gym class"></div>Gym Fitness<span class="time">9:00 - 10:00</span></div>
    <div class="row"><div class="thumb" role="img" aria-label="Boxing class"></div>Boxing<span class="time">11:00 - 12:00</span></div>
    <div class="row"><div class="thumb" role="img" aria-label="Yoga class"></div>Yoga Pilates<span class="time">17:00 - 18:00</span></div>
  </div>
  <div class="offer membership">
    <h3>Membership</h3>
    <div class="body"><div class="ring"><svg width="18" height="18"><circle cx="9" cy="9" r="6" fill="none" stroke="#fff" stroke-width="2"/></svg></div>
      <p>Join daily, monthly, six months or yearly with no hidden charges or fees.</p></div>
    <span class="btn">More Details</span>
  </div>
  <div class="offer training">
    <h3>Personal Training</h3>
    <div class="body"><div class="ring"><svg width="18" height="18"><path d="M3 9h12M5 5v8M13 5v8" stroke="#fff" stroke-width="2"/></svg></div>
      <p>Bring your own trainer at no entry charge, or book one of our experts.</p></div>
    <span class="btn">More Details</span>
  </div>
</section>

<section class="about abs">
  <div class="about-photo" role="img" aria-label="Members training on exercise bikes"></div>
  <div class="about-panel">
    <h2>ABOUT THE CLUB</h2>
    <p>We are gym people building the club we always wanted: the biggest space in the country, two huge activity rooms, equipment second to none and five star service. No hidden fees, no forced trainers, just quality and the right attitude every single day.</p>
    <span class="btn">Read More &#9656;</span>
  </div>
</section>

<main class="articles abs">
  <div class="bar"><h2>LATEST ARTICLES</h2><span>VIEW ALL</span></div>

  <article class="article">
    <div class="date"><b>29</b><i>MAR</i><small>3 Comments<br>Admin</small></div>
    <div class="photo ph-1" role="img" aria-label="Rows of dumbbells on a rack"></div>
    <h3>LOREM IPSUM DOLOR SIT AMAT VELUM</h3>
    <p>Our new training floor opens this spring with fresh racks, longer hours and more room for every member to move, lift and recover. Come early, meet the team and try a free class on opening week.</p>
    <span class="btn">Read More</span>
  </article>

  <article class="article">
    <div class="date"><b>29</b><i>MAR</i><small>3 Comments<br>Admin</small></div>
    <div class="photo ph-2" role="img" aria-label="Two members smiling during a workout"></div>
    <h3>LOREM IPSUM DOLOR SIT AMAT VELUM</h3>
    <p>Freelance trainers can now run sessions in our activity rooms. Grow your client base, book the space you need and let members discover your style without any extra entry charges at all.</p>
    <span class="btn">Read More</span>
  </article>

  <article class="article">
    <div class="date"><b>29</b><i>MAR</i><small>3 Comments<br>Admin</small></div>
    <div class="photo ph-3" role="img" aria-label="Gym training scene"></div>
    <h3>LOREM IPSUM DOLOR SIT AMAT VELUM</h3>
    <p>The brawnmesh box timetable is live with classes from top coaches across the country, every morning and evening.</p>
    <span class="btn">Read More</span>
  </article>
</main>

<aside class="sidebar abs">
  <div class="widget">
    <div class="widget-title">TRAINING CLASSES</div>
    <div class="acc"><div><b>Gym Fitness</b><small>Strength, speed, stamina</small></div><span class="plus">+</span></div>
    <div class="acc"><div><b>Indoor Cycling</b><small>Strength, speed, stamina</small></div><span class="plus">+</span></div>
    <div class="acc"><div><b>Yoga Pilates</b><small>Calm, flexible, focused</small></div><span class="plus">&minus;</span></div>
    <div class="acc-open"><div class="thumb" role="img" aria-label="Yoga class in session"></div><div>Gentle flow sessions for balance and core strength.<br><em>Time Table</em> &nbsp; <em>Details</em></div></div>
    <div class="acc"><div><b>Cardio Fitness</b><small>Heart, lungs, endurance</small></div><span class="plus">+</span></div>
  </div>

  <div class="widget">
    <div class="widget-title">EVENT CALENDAR</div>
    <div class="calendar">
      <div class="month">February, 2015</div>
      <table>
        <tr><th>M</th><th>T</th><th>W</th><th>T</th><th>F</th><th>S</th><th>S</th></tr>
        <tr><td></td><td></td><td></td><td></td><td></td><td></td><td>1</td></tr>
        <tr><td>2</td><td>3</td><td>4</td><td>5</td><td>6</td><td>7</td><td>8</td></tr>
        <tr><td>9</td><td>10</td><td>11</td><td>12</td><td>13</td><td>14</td><td>15</td></tr>
        <tr><td>16</td><td>17</td><td>18</td><td>19</td><td class="today">20</td><td>21</td><td>22</td></tr>
        <tr><td>23</td><td>24</td><td>25</td><td>26</td><td>27</td><td>28</td><td></td></tr>
      </table>
    </div>
  </div>

  <div class="widget">
    <div class="widget-title">SNAPVAULT</div>
    <div class="insta">
      <div class="g1" role="img" aria-label="Member photo"></div><div class="g2" role="img" aria-label="Gym floor photo"></div><div class="g3" role="img" aria-label="Class photo"></div><div class="g4" role="img" aria-label="Training photo"></div>
      <div class="g3" role="img" aria-label="Class photo"></div><div class="g4" role="img" aria-label="Training photo"></div><div class="g1" role="img" aria-label="Member photo"></div><div class="g2" role="img" aria-label="Gym floor photo"></div>
    </div>
  </div>
</aside>

<footer class="site-footer abs">
  <div class="footer-cols abs">
    <div class="contact">
      <h4>Contact Info</h4>
      <div>14 Harbour Lane, Unit 7<br>Palm District 00412<br>Phone: +000 555 0142<br>hello@ironhall.example</div>
    </div>
    <div class="links">
      <div><h4>Quick Links</h4>Membership<br>Classes<br>Contact Us</div>
      <div><h4>&nbsp;</h4>Privacy Policy<br>Terms &amp; Conditions<br>Location</div>
    </div>
    <div class="news">
      <h4>Newsletter Signup</h4>
      <div>Sign up for our newsletter and get the latest news.</div>
      <form><div class="field"></div><span class="btn">Submit</span></form>
    </div>
  </div>
  <div class="copyright abs">Copyright &copy; 2015 Ironhall. All rights reserved.</div>
</footer>

</body>
</html>
```